"Harbor Builders" is a residential building company and needs a new business card design and may re

We would like a redesign based on the existing logo, and would like to see a new font as well. We are bespoke home builders who build sustainable energy efficient homes.

Industry/Entity Type

Construction

Contact Information for Business Card

Business card size 40mm x 90mm

Colors

Designer to choose colors to be used in the design.

```html
<!DOCTYPE html>
<html lang="en">
<head>
<meta charset="utf-8">
<title>Harbor Builders – Business Card</title>
<link href="https://fonts.googleapis.com/css2?family=Roboto:wght@400;500;700&family=Roboto+Condensed:wght@700&display=swap" rel="stylesheet">
<style>
  :root {
    --backdrop: #e8e5e0;
    --card-light: #f4f4f4;
    --card-dark: #1c1d1f;
    --lime: #c0d83a;
    --ink: #1e1e1e;
    --text-grey: #4a4a4a;
  }
  * { margin: 0; padding: 0; box-sizing: border-box; }
  html, body {
    width: 1200px; height: 960px; overflow: hidden;
    background: var(--backdrop);
    font-family: "Roboto", Arial, sans-serif;
  }
  .canvas { position: relative; width: 1200px; height: 960px; }

  .card { position: absolute; box-shadow: 0 3px 8px rgba(0,0,0,.25); }

  /* Front */
  .card-front {
    left: 302px; top: 129px; width: 601px; height: 342px;
    background: var(--card-light);
  }
  .side-strip {
    position: absolute; left: 30px; top: 0; width: 98px; height: 100%;
    background: var(--card-dark);
  }
  .side-strip-cap {
    position: absolute; left: 0; top: 0; width: 100%; height: 56px;
    background: var(--lime);
  }
  .strip-icon { position: absolute; left: 40px; width: 16px; height: 16px; }
  .brand-name {
    position: absolute; left: 138px; top: 48px;
    font-family: "Roboto", Arial, sans-serif; font-weight: 700;
    font-size: 27px; color: var(--ink); letter-spacing: -0.3px;
  }
  .holder-name {
    position: absolute; left: 139px; top: 113px;
    font-family: "Roboto Condensed", "Arial Narrow", sans-serif;
    font-weight: 700; font-size: 22px; color: var(--ink);
  }
  .details {
    position: absolute; left: 140px;
    font-size: 14.5px; line-height: 18.5px; color: var(--text-grey);
  }
  .details strong { font-weight: 500; }
  .details-company { top: 148px; }
  .details-registry { top: 205px; }
  .details-contact { top: 247px; line-height: 19.5px; }

  /* Back */
  .card-back {
    left: 299px; top: 489px; width: 600px; height: 341px;
    background: var(--card-dark);
  }
  .back-brand {
    position: absolute; left: 0; top: 128px; width: 100%;
    text-align: center; font-family: "Roboto", Arial, sans-serif;
    font-weight: 700; font-size: 42px; color: var(--lime);
  }
  .back-web {
    position: absolute; left: 0; top: 295px; width: 100%;
    text-align: center; font-size: 14px; letter-spacing: 2.6px;
    color: var(--lime);
  }
</style>
</head>
<body>
<main class="canvas">

  <section class="card card-front" aria-label="Card front">
    <div class="side-strip">
      <div class="side-strip-cap"></div>
      <svg class="strip-icon" style="top:150px" viewBox="0 0 16 16" aria-hidden="true">
        <path d="M8 1a5 5 0 0 0-5 5c0 3.8 5 9 5 9s5-5.2 5-9a5 5 0 0 0-5-5zm0 7a2 2 0 1 1 0-4 2 2 0 0 1 0 4z" fill="var(--lime)"/>
      </svg>
      <svg class="strip-icon" style="top:248px" viewBox="0 0 16 16" aria-hidden="true">
        <rect x="4.5" y="1" width="7" height="14" rx="1.2" fill="none" stroke="var(--lime)" stroke-width="1.4"/>
        <rect x="7" y="12" width="2" height="1.3" fill="var(--lime)"/>
      </svg>
      <svg class="strip-icon" style="top:270px" viewBox="0 0 16 16" aria-hidden="true">
        <rect x="2" y="4" width="12" height="8.5" fill="var(--lime)"/>
        <path d="M2 4l6 5 6-5" fill="none" stroke="var(--card-dark)" stroke-width="1.2"/>
      </svg>
      <svg class="strip-icon" style="top:289px" viewBox="0 0 16 16" aria-hidden="true">
        <circle cx="8" cy="8" r="6" fill="var(--lime)"/>
        <path d="M5 5c1 .5 2 0 3 1s0 2 1 3 2 0 2 2M9 3.5c0 1 1 1.5 2 1.5" fill="none" stroke="var(--card-dark)" stroke-width="1.1"/>
      </svg>
    </div>

    <div class="brand-name">Harbor Builders</div>
    <h1 class="holder-name">DANIEL MORROW</h1>

    <p class="details details-company">
      <strong>Harbor Builders Pty Ltd</strong><br>
      PO Box 4127 Eastgate<br>
      LPO Ridgeview WA 6099
    </p>
    <p class="details details-registry">
      Registration 48315<br>
      ABN: 52 904 316 778
    </p>
    <p class="details details-contact">
      0400 555 318<br>
      daniel@harborbuilders.com.au<br>
      www.harborbuilders.com.au
    </p>
  </section>

  <section class="card card-back" aria-label="Card back">
    <div class="back-brand">Harbor Builders</div>
    <div class="back-web">www.harborbuilders.com.au</div>
  </section>

</main>
</body>
</html>
```